BuildLinkHub.com Full Stationery Design

Business Card will have all info on it. Letterhead will not have name, title or mobile number. Keep general feeling very clean, using colors from the logo as accents.
Name:Dale Marchetti
Title:President
Phone: 1-800-555-0142
Cell: 555-555-0187
email: dale@buildlinkhub.example
website: www.buildlinkhub.example
Address:
PO Box 947
Pinecrest, MB
R0X1Y0

Target Market(s)

Construction Business owners

Industry/Entity Type

Business

Contact Information for Business Card

Name:Dale Marchetti
Title:President
Phone: 1-800-555-0142
Cell: 555-555-0187
Address:
PO Box 947
Pinecrest, MB
R0X1Y0

Font styles to use
Sans Serif

Requirements
Must have
• Clean look
Should not have
• Images or cartoon type characters or tools

```html
<!DOCTYPE html>
<html lang="en">
<head>
<meta charset="utf-8">
<title>BuildLinkHub.com Stationery</title>
<link href="https://fonts.googleapis.com/css2?family=Questrial&family=Roboto:wght@400;700&display=swap" rel="stylesheet">
<style>
  :root {
    --orange: #ec5a1c;
    --orange-dark: #d94a12;
    --slate: #4a5563;
    --slate-light: #7d8794;
    --paper: #ffffff;
    --pattern-grey: #eceef0;
    --backdrop: #f7c8ab;
    --text: #3d4450;
  }
  * { box-sizing: border-box; margin: 0; padding: 0; }
  html, body { width: 1200px; height: 900px; overflow: hidden; }
  body {
    background: linear-gradient(180deg, #fbe3d3 0%, var(--backdrop) 100%);
    font-family: "Roboto", sans-serif;
    color: var(--text);
    position: relative;
  }
  .piece {
    position: absolute;
    background: var(--paper);
    box-shadow: 0 4px 14px rgba(120, 60, 30, 0.18);
    overflow: hidden;
  }
  .brand {
    display: flex;
    align-items: center;
    gap: 7px;
    font-family: "Questrial", sans-serif;
    color: var(--slate);
    white-space: nowrap;
  }
  .brand-mark { background: var(--orange); flex: none; }
  .brand--light { color: #fff; }
  .brand--light .brand-mark { background: #fff; }

  .accent-bar {
    position: absolute; left: 0; right: 0; bottom: 0; height: 5px;
    background: linear-gradient(90deg, var(--orange) 0 78%, var(--slate-light) 78% 100%);
  }
  .edge-tick {
    position: absolute; width: 4px; height: 16px;
    background: linear-gradient(var(--orange) 0 50%, var(--slate-light) 50% 100%);
  }

  .contact-list { list-style: none; font-size: 7px; line-height: 1.6; color: var(--text); white-space: nowrap; }
  .contact-list li { display: flex; align-items: center; gap: 4px; }
  .contact-list li::before {
    content: ""; width: 5px; height: 5px; border-radius: 50%; background: var(--orange); flex: none;
  }

  /* Business card back */
  .card-back { left: 50px; top: 40px; width: 330px; height: 185px; border-radius: 10px; }
  .card-back .pattern { position: absolute; inset: 0; background: linear-gradient(135deg, var(--orange) 0%, var(--orange-dark) 100%); }
  .card-back .brand { position: absolute; left: 50%; top: 50%; transform: translate(-50%, -50%); font-size: 26px; }
  .card-back .brand-mark { width: 26px; height: 26px; }

  /* Business card front */
  .card-front { left: 50px; top: 250px; width: 330px; height: 185px; border-radius: 10px; }
  .card-front .brand { position: absolute; left: 18px; top: 86px; font-size: 15px; }
  .card-front .brand-mark { width: 15px; height: 15px; }
  .card-front .person { position: absolute; left: 186px; top: 26px; }
  .person-name { font-size: 12px; font-weight: 700; color: var(--orange); }
  .person-title { font-size: 7.5px; font-weight: 700; color: var(--slate); margin-bottom: 6px; }

  /* Letterhead */
  .letterhead { left: 450px; top: 40px; width: 320px; height: 420px; }
  .letterhead .brand { position: absolute; left: 20px; top: 22px; font-size: 12px; }
  .letterhead .brand-mark { width: 13px; height: 13px; }
  .letterhead .contact-list { position: absolute; right: 16px; top: 22px; font-size: 5px; }
  .letterhead .edge-tick { top: 22px; left: 0; }
  .letterhead .edge-tick--right { left: auto; right: 0; }

  /* Presentation folder */
  .folder { left: 800px; top: 150px; width: 360px; height: 470px; }
  .folder .pattern { position: absolute; inset: 0; background: var(--pattern-grey); }
  .folder .brand { position: absolute; left: 50%; top: 46%; transform: translate(-50%, -50%); font-size: 28px; }
  .folder .brand-mark { width: 30px; height: 30px; }

  /* Compliment slip */
  .slip { left: 50px; top: 470px; width: 340px; height: 165px; }
  .slip .brand { position: absolute; left: 20px; top: 22px; font-size: 11px; }
  .slip .brand-mark { width: 12px; height: 12px; }
  .slip .contact-list { position: absolute; right: 14px; top: 18px; font-size: 5px; }
  .slip .edge-tick { top: 20px; left: 0; }
  .slip .edge-tick--right { left: auto; right: 0; }

  /* Envelope */
  .envelope { left: 50px; top: 665px; width: 350px; height: 195px; }
  .envelope .pattern { position: absolute; inset: 0; background: #f4f5f6; }
  .envelope .flap { position: absolute; left: 0; right: 0; top: 0; height: 44px; background: var(--orange); border-radius: 0 0 40% 40% / 0 0 30px 30px; }
  .envelope .brand { position: absolute; left: 50%; bottom: 28px; transform: translateX(-50%); font-size: 15px; }
  .envelope .brand-mark { width: 15px; height: 15px; }

  /* Pen */
  .pen { left: 450px; top: 650px; width: 480px; height: 40px; border-radius: 4px 20px 20px 4px; }
  .pen .brand { position: absolute; top: 50%; transform: translateY(-50%); font-size: 12px; }
  .pen .brand--barrel { left: 140px; }
  .pen .brand--clip { left: 340px; }
  .pen .brand-mark { width: 12px; height: 12px; }

  /* Erasers */
  .eraser { width: 140px; height: 64px; border-radius: 4px; }
  .eraser--one { left: 630px; top: 730px; }
  .eraser--two { left: 820px; top: 775px; }
  .eraser .brand { position: absolute; left: 50%; top: 50%; transform: translate(-50%, -50%); font-size: 10px; }
  .eraser .brand-mark { width: 10px; height: 10px; }
</style>
</head>
<body>

  <section class="piece card-back">
    <div class="pattern" role="img" aria-label="Repeating geometric pattern in orange tones"></div>
    <div class="brand brand--light"><span class="brand-mark"></span>BuildLinkHub.com</div>
  </section>

  <section class="piece card-front">
    <div class="brand"><span class="brand-mark"></span>BuildLinkHub.com</div>
    <div class="person">
      <p class="person-name">Dale Marchetti</p>
      <p class="person-title">President</p>
      <ul class="contact-list">
        <li>PO Box 947, Pinecrest, MB, R0X1Y0</li>
        <li>1-800-555-0142</li>
        <li>555-555-0187</li>
        <li>dale@buildlinkhub.example</li>
        <li>www.buildlinkhub.example</li>
      </ul>
    </div>
    <div class="accent-bar"></div>
  </section>

  <section class="piece letterhead">
    <span class="edge-tick"></span><span class="edge-tick edge-tick--right"></span>
    <div class="brand"><span class="brand-mark"></span>BuildLinkHub.com</div>
    <ul class="contact-list">
      <li>PO Box 947, Pinecrest, MB, R0X1Y0</li>
      <li>Phone: 1-800-555-0142</li>
      <li>dale@buildlinkhub.example</li>
      <li>www.buildlinkhub.example</li>
    </ul>
    <div class="accent-bar"></div>
  </section>

  <section class="piece folder">
    <div class="pattern" role="img" aria-label="Light grey repeating geometric pattern"></div>
    <div class="brand"><span class="brand-mark"></span>BuildLinkHub.com</div>
    <div class="accent-bar"></div>
  </section>

  <section class="piece slip">
    <span class="edge-tick"></span><span class="edge-tick edge-tick--right"></span>
    <div class="brand"><span class="brand-mark"></span>BuildLinkHub.com</div>
    <ul class="contact-list">
      <li>PO Box 947, Pinecrest, MB, R0X1Y0</li>
      <li>Phone: 1-800-555-0142</li>
      <li>dale@buildlinkhub.example</li>
      <li>www.buildlinkhub.example</li>
    </ul>
    <div class="accent-bar"></div>
  </section>

  <section class="piece envelope">
    <div class="pattern" role="img" aria-label="Faint grey repeating geometric pattern"></div>
    <div class="flap"></div>
    <div class="brand"><span class="brand-mark"></span>BuildLinkHub.com</div>
  </section>

  <section class="piece pen">
    <div class="brand brand--barrel"><span class="brand-mark"></span>BuildLinkHub.com</div>
    <div class="brand brand--clip"><span class="brand-mark"></span>BuildLinkHub.com</div>
  </section>

  <section class="piece eraser eraser--one">
    <div class="brand"><span class="brand-mark"></span>BuildLinkHub.com</div>
  </section>

  <section class="piece eraser eraser--two">
    <div class="brand"><span class="brand-mark"></span>BuildLinkHub.com</div>
  </section>

</body>
</html>
```